New Dental Office Needs an Attractive and user friendly Website Designed

I need a website for a new dental office. The Name is Harrowfield Dentistry. I would like a Modern design with a user friendly interface and usability.
I would like a landing page, a page that lists the services we offer: Cosmetic Dentistry, Implants, Dental Hygiene, Emergency Services, Restorations, Dentures
Target Market(s)
Mid to upper class
Industry/Entity Type
Dentistry
Coding
Number of Pages Required
1 page
Requirements
Must have
- Landing page that has a scheduling option, Procedures, operating hours, and contact us info
Nice to have
- Appealing design, Soft comforting colors. Easy to navigate page, Modern and professional.

```html
<!DOCTYPE html>
<html lang="en"><head><meta charset="utf-8"><title>Harrowfield Dentistry – Website Design Board</title>
<link href="https://fonts.googleapis.com/css2?family=Plus+Jakarta+Sans:wght@400;500;600;700&display=swap" rel="stylesheet">
<style>
:root{--board:#4b4b4b;--teal:#0f5f63;--teal-mid:#2d8689;--teal-soft:#5fa9ab;--accent:#17a2a7;--mist:#eef5f5;--ink:#12343a;--muted:#7a8c8f;--line:#dbe6e6;--white:#fff;--star:#f4b400}
*{box-sizing:border-box;margin:0;padding:0}
html,body{width:1200px;height:986px;overflow:hidden;background:var(--board);font-family:"Plus Jakarta Sans",sans-serif;color:var(--ink)}
.board{position:absolute;left:0;top:0;width:2113px;height:1736px;transform:scale(.5679);transform-origin:0 0}
.a{position:absolute}
.page{position:absolute;background:var(--white);overflow:hidden}
.ph{position:absolute;background:linear-gradient(135deg,#9cc4c5,#4d8f91)}
.ph.warm{background:linear-gradient(135deg,#e9d3c4,#b98f78)}
.ph.grey{background:linear-gradient(135deg,#c9cfcf,#7f8b8c)}
.logo{font-weight:600;font-size:9px;color:var(--ink);white-space:nowrap}
.logo.light{color:var(--white)}
.nav{position:absolute;display:flex;align-items:center;gap:10px;height:26px;padding:0 14px;background:var(--white);border-radius:8px;font-size:5px;color:var(--ink)}
.nav ul{display:flex;gap:9px;list-style:none;flex:1;margin-left:18px}
.nav li,.links li{white-space:nowrap}
.btn{display:inline-block;background:var(--accent);color:var(--white);font-size:5.5px;font-weight:600;padding:5px 8px;border-radius:3px;white-space:nowrap}
.btn.white{background:var(--white);color:var(--accent)}
.hero{position:absolute;width:462px;background:var(--teal);overflow:hidden}
.hero.mid{background:var(--teal-mid)}
.hero-copy{position:absolute;color:var(--white)}
.hero-copy .kick{font-size:5.5px;margin-bottom:5px}
.hero-copy h2{font-weight:500;font-size:19px;line-height:1.3;margin-bottom:8px}
.hero-copy p{font-size:5.5px;line-height:1.7;width:170px;opacity:.9;margin-bottom:10px}
.rating{font-size:5.5px;color:var(--white);margin-top:28px;white-space:nowrap}
.rating b{color:var(--star);font-weight:500}
.topbar{position:absolute;left:0;top:0;width:462px;height:18px;background:var(--teal);color:var(--white);font-size:4.8px;display:flex;align-items:center;gap:14px;padding:0 24px;white-space:nowrap}
.info-strip{position:absolute;display:flex;justify-content:space-between;background:var(--white);font-size:5px;color:var(--muted);line-height:1.6}
.info-strip b{display:block;color:var(--ink);font-weight:600;font-size:6px}
.kicker{font-size:5px;font-weight:600;color:var(--ink)}
.h-sec{font-size:13px;font-weight:600;color:var(--ink)}
.small{font-size:5px;line-height:1.7;color:var(--muted)}
.stat{position:absolute;background:var(--mist);border-radius:6px;padding:10px}
.stat .lab{font-size:8px;color:var(--muted);line-height:1.3}
.stat .num{position:absolute;left:10px;bottom:8px;font-size:16px;font-weight:500;color:var(--ink)}
.svc-row{position:absolute;left:27px;width:406px;height:48px;border-bottom:1px solid var(--line);display:flex;align-items:center}
.svc-row h4{font-size:9.5px;font-weight:600;width:154px;padding-left:20px}
.svc-row p{font-size:5px;color:var(--muted);width:150px;line-height:1.6}
.arrow-c{position:absolute;right:6px;width:16px;height:16px;border-radius:50%;border:1px solid var(--line);color:var(--accent);font-size:8px;display:flex;align-items:center;justify-content:center}
.member{position:absolute;width:80px;text-align:center}
.member .ph{position:relative;width:46px;height:46px;margin:0 auto 5px;border-radius:50%}
.member b{display:block;font-size:5.5px;font-weight:600}
.member span{font-size:4.5px;color:var(--accent)}
.faq-row{position:absolute;left:14px;width:170px;border-bottom:1px solid var(--line);padding-bottom:10px;font-size:6px;font-weight:600;display:flex;justify-content:space-between}
.field{position:absolute;font-size:5px;color:var(--ink)}
.field span{display:block;margin-top:5px;width:90px;height:17px;background:var(--white);border:1px solid var(--line);border-radius:3px;font-size:4.5px;color:#b7c3c4;padding:5px}
.foot-col{position:absolute;color:var(--white);font-size:5px;line-height:2.6;white-space:nowrap}
.foot-col b{display:block;font-size:6.5px;font-weight:600;line-height:1.4;margin-bottom:6px}
.why{position:absolute;width:120px}
.why .ic{width:18px;height:18px;background:var(--teal);border-radius:4px;margin-bottom:8px}
.why b{display:block;font-size:6.5px;font-weight:600;margin-bottom:4px}
</style></head><body>
<div class="board">

<main class="page" style="left:46px;top:36px;width:462px;height:1654px">
 <section class="a" style="left:0;top:0;width:462px;height:260px;background:var(--teal-mid)">
  <div class="ph" style="left:230px;top:0;width:232px;height:260px;background:linear-gradient(135deg,#5fa5a7,#2e7d80)" role="img" aria-label="Smiling dentist in white coat in a clinic"></div>
  <span class="a logo light" style="left:27px;top:10px">Harrowfield Dentistry</span>
  <ul class="a links" style="left:128px;top:14px;display:flex;gap:8px;list-style:none;font-size:5px;color:var(--white)"><li>Home</li><li>About us</li><li>Services</li><li>Testimonials</li><li>Case studies</li><li>Gallery</li><li>Blogs</li></ul>
  <div class="a" style="left:364px;top:8px;width:16px;height:16px;border-radius:4px;background:var(--accent)"></div>
  <div class="a" style="left:388px;top:8px;font-size:5px;color:var(--white);line-height:1.6;white-space:nowrap">Call us any time<br><b style="font-size:6px">+1 212 555 0192</b></div>
  <div class="hero-copy" style="left:27px;top:60px">
   <div class="kick">✦ Welcome to the Harrowfield</div>
   <h2 style="font-size:21px">Get your confident<br>smile now!</h2>
   <p style="width:205px">At our practice, excellence in dentistry goes hand-in-hand with personalized care, offering patients of all ages a wide range of tailored dental solutions.</p>
   <span class="btn white">Book an appointment →</span>
   <div class="rating" style="margin-top:24px">Patient Rating <b>5.0 ★★★★★</b> based on 492 reviews</div>
  </div>
 </section>
 <section class="a" style="left:0;top:260px;width:462px;height:51px;background:var(--mist)">
  <div class="a" style="left:27px;top:8px;font-size:20px;font-weight:500">8k+</div>
  <div class="a" style="left:27px;top:36px;font-size:5px">Happy Patients</div>
  <p class="a small" style="left:92px;top:12px;width:150px">Let's bring your perfect smile to life! Whether you need a complete smile makeover or routine dental care, we've got you covered.</p>
 </section>
 <div class="a" style="left:300px;top:214px;width:135px;height:97px;background:var(--teal);color:var(--white);padding:12px 13px">
  <b style="font-size:7px;font-weight:600;display:block;line-height:1.4">Ready for a Stunning Smile Transformation?</b>
  <p style="font-size:4.8px;line-height:1.6;margin-top:6px;opacity:.85">Book an appointment today and let us help you achieve the healthy, beautiful smile you deserve!</p>
  <div style="font-size:6px;font-weight:600;margin-top:10px;display:flex;justify-content:space-between">Book an Appointment <span>→</span></div>
 </div>
 <section class="a" style="left:0;top:311px;width:462px;height:278px">
  <div class="ph" style="left:27px;top:42px;width:82px;height:62px;border-radius:30px" role="img" aria-label="Dentist at work in treatment room"></div>
  <div class="a" style="left:147px;top:44px;font-size:16px;font-weight:500">10+</div>
  <div class="a" style="left:182px;top:45px;font-size:4.5px;line-height:1.4">Years of<br>Experience</div>
  <div class="ph" style="left:107px;top:75px;width:107px;height:157px;border-radius:54px" role="img" aria-label="Dentist wearing mask and gloves"></div>
  <div class="kicker a" style="left:246px;top:44px">About Us</div>
  <h2 class="a" style="left:245px;top:63px;font-size:16px;font-weight:600;line-height:1.35">Welcome to<br>Harrowfield Dentistry!</h2>
  <p class="a small" style="left:245px;top:114px;width:190px">We are on a mission to bring smile on people's face since 2011. Harrowfield Dentistry is conveniently located in Los Angeles where we make sure that we provide our patients with best facilities and a seamless dentistry experience.</p>
  <ul class="a" style="left:245px;top:162px;list-style:none;font-size:5px;line-height:2.4;width:190px">
   <li>● Advanced Technology For Optimal Patient Comfort.</li>
   <li>● Happy Patients From Los Angeles, USA, And Around The World</li>
   <li>● Expert Teams In Preventive And Curative Dentistry.</li>
   <li>● Focus On Aesthetic Value In All Treatments.</li></ul>
  <div class="ph" style="left:245px;top:228px;width:18px;height:18px;border-radius:3px" role="img" aria-label="Portrait of the practice owner"></div>
  <div class="a" style="left:271px;top:229px;font-size:6px;font-weight:600">Dr. Miles Garrow<div style="font-size:4.8px;color:var(--muted);font-weight:400;margin-top:2px">Owner and Director</div></div>
 </section>
 <section class="a" style="left:0;top:589px;width:462px;height:437px;background:var(--mist)">
  <h3 class="a" style="left:0;top:33px;width:462px;text-align:center;font-size:12px;font-weight:600">Enjoy Specialized Dental Services</h3>
  <div class="svc-row" style="top:62px"><h4>Dental Implants</h4><p>The implant is a medical device made of titanium which serves as the root for missing tooth on top of...</p><span class="arrow-c">↗</span></div>
  <div class="svc-row" style="top:122px;background:var(--white);border-radius:6px;height:52px;left:32px;width:398px"><h4 style="color:var(--accent)">Cosmetic Dentistry ↗</h4><p>The implant is a medical device made of titanium which serves as the root for missing tooth on top of...</p><div class="ph" style="right:8px;top:5px;width:68px;height:42px;border-radius:21px" role="img" aria-label="Patient in dental chair"></div></div>
  <div class="svc-row" style="top:185px"><h4>Dental Hygiene</h4><p>Bleeding gums when brushing is common but not normal and should never be ignored. It may indicate...</p><span class="arrow-c">↗</span></div>
  <div class="svc-row" style="top:234px"><h4>Emergency Services</h4><p>Tooth colored resin-based light-cured cement which bonds to the tooth surface. We try and do co...</p><span class="arrow-c">↗</span></div>
  <div class="svc-row" style="top:283px"><h4>Restorations</h4><p>Tooth pain is the 2nd most unbearable pain. It can be caused due to many reasons.</p><span class="arrow-c">↗</span></div>
  <div class="svc-row" style="top:332px"><h4>Dentures</h4><p>Tooth pain is the 2nd most unbearable pain. It can be caused due to many reasons.</p><span class="arrow-c">↗</span></div>
  <div class="a" style="left:184px;top:393px;display:flex;gap:7px;font-size:5px">
   <span>←</span><span style="background:var(--accent);color:#fff;border-radius:50%;width:13px;height:13px;text-align:center;line-height:13px">1</span><span style="width:13px;text-align:center">2</span><span style="width:13px;text-align:center">3</span><span>→</span></div>
 </section>
 <section class="a" style="left:0;top:1026px;width:462px;height:334px">
  <div class="kicker a" style="left:27px;top:32px">See the transformation</div>
  <h3 class="a h-sec" style="left:27px;top:42px">Smile Gallery</h3>
  <p class="a small" style="left:283px;top:31px;width:152px">The dream of having a perfect smile isn't far-fetched. We'll be happy to contribute in giving you a smile that you love and a smile that you can feel confident in.</p>
  <div class="a" style="left:4px;top:147px;font-size:20px;font-weight:700;color:#c9e2e2">EAL RESU</div>
  <div class="a" style="left:352px;top:147px;font-size:20px;font-weight:700;color:#c9e2e2">REAL RES</div>
  <div class="a" style="left:112px;top:80px;width:237px;height:200px;background:var(--mist);border-radius:6px">
   <div class="ph warm" style="left:4px;top:0;width:229px;height:155px" role="img" aria-label="Before and after teeth whitening smile"></div>
   <div class="a" style="left:0;top:168px;width:237px;text-align:center;font-size:5px;color:var(--muted)">TREATMENTS</div>
   <div class="a" style="left:0;top:180px;width:237px;text-align:center;font-size:7px;color:var(--teal)">Teeth Whitening</div>
  </div>
 </section>
 <section class="a" style="left:0;top:1360px;width:462px;height:169px;background:var(--mist)">
  <div class="kicker a" style="left:27px;top:32px">See the difference by yourself</div>
  <h3 class="a h-sec" style="left:27px;top:42px">Why choose us?</h3>
  <p class="a small" style="left:283px;top:32px;width:152px">We have built an environment of trust and comfort with our patients by using the latest technology and providing best services in cost efficient way.</p>
  <div class="why" style="left:27px;top:80px"><div class="ic"></div><b>High Standard of Dentistry</b><p class="small">We provide excellent dentistry experience by using latest technology.</p></div>
  <div class="why" style="left:173px;top:80px"><div class="ic"></div><b>Committed Dental Team</b><p class="small">We are a dedicated team of dentists who are passionate about what they do.</p></div>
  <div class="why" style="left:318px;top:80px"><div class="ic"></div><b>Modern Equipments</b><p class="small">The key to provide better dentistry experience is to evolve with time.</p></div>
 </section>
 <section class="a" style="left:0;top:1529px;width:462px;height:125px">
  <div class="kicker a" style="left:27px;top:30px">Clinic figures</div>
  <h3 class="a h-sec" style="left:27px;top:40px">Our achievements so far!</h3>
  <p class="a small" style="left:283px;top:30px;width:152px">We have built an environment of trust and comfort with our patients by using the latest technology and providing best services in cost efficient way.</p>
  <div class="ph" style="left:27px;top:78px;width:94px;height:60px" role="img" aria-label="Smiling patient"></div>
  <div class="stat" style="left:132px;top:78px;width:94px;height:60px"><div class="lab">Brighter Smiles Achieved</div></div>
  <div class="ph" style="left:236px;top:78px;width:94px;height:60px" role="img" aria-label="Dentist treating patient"></div>
  <div class="stat" style="left:341px;top:78px;width:94px;height:60px"><div class="lab">Satisfied Patients and Counting</div></div>
 </section>
</main>

<main class="page" style="left:551px;top:0;width:462px;height:1690px">
 <section class="a" style="left:0;top:0;width:462px;height:293px">
  <div class="kicker a" style="left:27px;top:27px">Clinic figures</div>
  <h3 class="a h-sec" style="left:27px;top:36px">Our achievements so far!</h3>
  <p class="a small" style="left:283px;top:27px;width:152px">We have built an environment of trust and comfort with our patients by using the latest technology and providing best services in cost efficient way.</p>
  <div class="ph" style="left:27px;top:75px;width:94px;height:89px" role="img" aria-label="Smiling patient in dental chair"></div>
  <div class="stat" style="left:132px;top:75px;width:94px;height:89px"><div class="lab">Brighter Smiles Achieved</div><div class="num">500+</div></div>
  <div class="ph" style="left:236px;top:75px;width:94px;height:89px" role="img" aria-label="Dentist examining patient"></div>
  <div class="stat" style="left:341px;top:75px;width:94px;height:89px"><div class="lab">Satisfied Patients and Counting</div><div class="num">8k+</div></div>
  <div class="stat" style="left:27px;top:175px;width:94px;height:89px"><div class="lab">Successful Root Canal Treatments</div><div class="num">2500+</div></div>
  <div class="ph" style="left:132px;top:175px;width:94px;height:89px" role="img" aria-label="Dental treatment in progress"></div>
  <div class="stat" style="left:236px;top:175px;width:94px;height:89px"><div class="lab">Successful Implant Surgeries</div><div class="num">750+</div></div>
  <div class="ph" style="left:341px;top:175px;width:94px;height:89px" role="img" aria-label="Dental team at work"></div>
 </section>
 <section class="a" style="left:0;top:293px;width:462px;height:302px;background:var(--mist)">
  <div class="member" style="left:37px;top:30px"><div class="ph" role="img" aria-label="Team member portrait"></div><b>Dr. Miles Garrow</b><span>Owner and director</span></div>
  <div class="member" style="left:136px;top:30px"><div class="ph" role="img" aria-label="Team member portrait"></div><b>Nora Pell</b><span>MDS, Oral &amp; Maxillofacial Surgery</span></div>
  <div class="member" style="left:37px;top:115px"><div class="ph" role="img" aria-label="Team member portrait"></div><b>Ivy Caldwell</b><span>MDS, Oral Medicine And Radiology</span></div>
  <div class="member" style="left:136px;top:115px"><div class="ph" role="img" aria-label="Team member portrait"></div><b>Rhea Solano</b><span>MDS, Oral &amp; Maxillofacial Surgery</span></div>
  <div class="member" style="left:37px;top:200px"><div class="ph" role="img" aria-label="Team member portrait"></div><b>Tessa Brandt</b><span>MDS, Oral Medicine And Radiology</span></div>
  <div class="member" style="left:136px;top:200px"><div class="ph" role="img" aria-label="Team member portrait"></div><b>Lena Okafor</b><span>MDS, Oral &amp; Maxillofacial Surgery</span></div>
  <div class="a" style="left:237px;top:30px;width:198px;height:236px;background:var(--white);border-radius:6px">
   <h3 class="a" style="left:14px;top:14px;font-size:12.5px;font-weight:600;color:var(--teal);line-height:1.6">Frequently Asked<br>Questions</h3>
   <div class="faq-row" style="top:64px;color:var(--accent);border:0">Will scaling weaken my teeth? <span style="color:var(--ink)">−</span></div>
   <p class="a small" style="left:14px;top:79px;width:170px;padding-bottom:8px;border-bottom:1px solid var(--line)">No, Scaling removes calculus and dirt deposited on your tooth making your gums healthy to hold your tooth for a longer time.</p>
   <div class="faq-row" style="top:121px">Are root canal treatment painful? <span>+</span></div>
   <div class="faq-row" style="top:153px">Are dental implants costly? <span>+</span></div>
   <div class="faq-row" style="top:185px">Are dental implants costly? <span>+</span></div>
   <div class="faq-row" style="top:217px;border:0">What if i dont get my missing teeth replaced? <span>+</span></div>
  </div>
 </section>
 <section class="a" style="left:0;top:621px;width:462px;height:242px;background:var(--teal)">
  <div class="ph warm" style="left:0;top:0;width:262px;height:242px" role="img" aria-label="Happy patient giving thumbs up in dental chair"></div>
  <div class="a" style="left:199px;top:0;width:201px;height:191px;background:var(--mist);padding:20px 8px">
   <div class="small">Testimonials</div>
   <h3 style="font-size:15px;font-weight:500;margin-top:16px"><b style="font-weight:600">Our happy</b> client says</h3>
   <div style="display:flex;gap:6px;margin-top:10px;align-items:center"><div class="ph warm" style="position:relative;width:16px;height:16px;border-radius:3px" role="img" aria-label="Client portrait"></div><div style="font-size:5.5px;font-weight:600">Owen Hartley<div style="font-weight:400;color:var(--muted);font-size:4.5px">Los Angeles</div></div><span style="margin-left:auto;color:var(--accent);font-size:12px">“</span></div>
   <p class="small" style="margin-top:10px">Cooperative staff, good quality treatment, came from out of town for dental treatment because of my previous good experience before 4 years. Appointment time were followed with punctuality and no waiting time. The way doctor explain treatment plan was really excellent. Moreover overall treatment cost was economical.</p>
   <div style="display:flex;gap:5px;margin-top:8px"><span class="btn" style="padding:3px 5px">←</span><span class="btn" style="padding:3px 5px">→</span></div>
  </div>
 </section>
 <section class="a" style="left:27px;top:892px;width:408px;height:224px">
  <div class="ph warm" style="left:0;top:0;width:198px;height:224px;border-radius:4px" role="img" aria-label="Dentist matching tooth shade guide to patient"></div>
  <div class="a" style="left:209px;top:0;width:199px;height:224px;background:var(--teal);border-radius:4px;color:var(--white);padding:14px 16px">
   <div style="font-size:5px">We highly encourage</div>
   <h3 style="font-size:12.5px;font-weight:600;margin:4px 0 6px">Lorem Ipsum dummy text</h3>
   <p style="font-size:5px;line-height:1.75;text-align:justify;opacity:.9">Lorem Ipsum is simply dummy text of the printing and typesetting industry. There are many variations of passages of Lorem Ipsum available, but the majority have suffered alteration in some form, by injected humour, or randomised words which don't look even slightly believable. If you are going to use a passage of Lorem Ipsum.<br><br>There are many variations of passages of Lorem Ipsum available, but the majority have suffered alteration in some form, by injected humour, or randomised words which don't look even slightly believable. If you are going to use a passage of Lorem Ipsum, you need to be sure there isn't anything embarrassing hidden in the middle of text. There are many variations of passages of Lorem Ipsum available, but the majority have suffered alteration in some form, by injected humour.<br><br>There are many variations of passages of Lorem Ipsum available, but the majority have suffered alteration in some form, by injected humour, or randomised words which don't look</p>
  </div>
 </section>
 <section class="a" style="left:0;top:1146px;width:462px;height:340px">
  <div class="ph grey" style="left:0;top:0;width:462px;height:230px" role="img" aria-label="Modern dental treatment room video still"></div>
  <div class="a" style="left:207px;top:106px;width:34px;height:34px;border-radius:50%;background:var(--white)"><svg width="34" height="34"><path d="M14 11 L24 17 L14 23Z" fill="#12343a"/></svg></div>
  <h3 class="a" style="left:27px;top:258px;font-size:13.5px;font-weight:500;line-height:1.3">Schedule Your<br>Appointment Now And<br>Take The First Step</h3>
  <div class="a" style="left:217px;top:189px;width:217px;height:151px;background:var(--mist);border-radius:6px">
   <h3 class="a" style="left:14px;top:12px;font-size:12px;font-weight:600">Book For Consultation</h3>
   <div class="field" style="left:14px;top:39px">Patient Name<span>Enter here</span></div>
   <div class="field" style="left:113px;top:39px">Phone Number<span>Enter here</span></div>
   <div class="field" style="left:14px;top:77px">Visit Date/Time<span>Select</span></div>
   <div class="field" style="left:113px;top:77px">Choose Service<span>Select</span></div>
   <span class="btn a" style="left:14px;top:117px;background:var(--teal);border-radius:9px;padding:6px 12px">Book Appointment</span>
  </div>
 </section>
 <footer class="a" style="left:27px;top:1513px;width:408px;height:160px;background:var(--teal);border-radius:6px">
  <span class="a logo light" style="left:22px;top:18px;font-size:8.5px">Harrowfield Dentistry</span>
  <div class="a" style="left:22px;top:44px;font-size:4.5px;color:var(--white)">Where amazing smiles begin!</div>
  <div class="foot-col" style="left:122px;top:16px"><b>Quick link</b>About Us<br>Services<br>Case studies<br>Testimonials<br>Blogs<br>Smile Gallery</div>
  <div class="foot-col" style="left:192px;top:16px;line-height:1.9"><b>Contact us</b>418 Larkmoor Ave. Fenwick,<br>Illinois 60412<br>☏ (252) 555-0148<br>✉ info@harrowfielddentistry.com</div>
  <div class="foot-col" style="left:296px;top:16px;line-height:2.2"><b>Clinic Timing</b>Mon to Sat 9:00 am to 12:30 pm<br>Mon to Sat 5:00 pm to 8:30 pm</div>
  <div class="a" style="left:22px;top:136px;font-size:5px;color:var(--white)">Copyright © 2021 Harrowfield Dentistry</div>
  <div class="a" style="left:288px;top:136px;font-size:5px;color:var(--white)">For emergency cases (252) 555-0148</div>
 </footer>
</main>

<section class="hero" style="left:1096px;top:40px;height:260px">
 <div class="ph" style="left:250px;top:0;width:212px;height:260px;background:linear-gradient(135deg,#2c7c7e,#b8434a)" role="img" aria-label="Smiling young woman"></div>
 <div class="nav" style="left:18px;top:8px;width:426px"><span class="logo">Harrowfield Dentistry</span><ul><li>Home</li><li>About us</li><li>Services</li><li>Testimonials</li><li>Case studies</li><li>Gallery</li><li>Blogs</li></ul><span class="btn">Book an appointment</span></div>
 <div class="hero-copy" style="left:57px;top:72px"><h2>Get your confident<br>smile now!</h2><p>Welcome to a place where excellence meets dentistry and patients of all ages experience wide range of personalised dental solutions.</p><span class="btn">Start using Brightline</span></div>
</section>

<section class="hero" style="left:1597px;top:40px;height:281px;background:var(--white)">
 <div class="a" style="left:0;top:0;width:462px;height:240px;background:var(--teal)"></div>
 <div class="ph" style="left:240px;top:0;width:222px;height:240px;background:linear-gradient(135deg,#2c7c7e,#b8434a)" role="img" aria-label="Smiling young woman"></div>
 <div class="nav" style="left:18px;top:8px;width:426px"><span class="logo">Harrowfield Dentistry</span><ul><li>Home</li><li>About us</li><li>Services</li><li>Testimonials</li><li>Case studies</li><li>Gallery</li><li>Blogs</li></ul><span class="btn">Contact Us</span></div>
 <div class="hero-copy" style="left:54px;top:54px"><div class="kick">Welcome to the Harrowfield</div><h2>Get your confident<br>smile now!</h2><p>At our practice, excellence in dentistry goes hand-in-hand with personalized care, offering patients of all ages a wide range of tailored dental solutions.</p><span class="btn">Book an appointment</span></div>
 <div class="info-strip" style="left:57px;top:215px;width:350px;height:45px;padding:8px 10px;border-radius:4px;box-shadow:0 2px 8px rgba(0,0,0,.12)">
  <div><b>Contact Us</b>+1 212 555 0192<br>info@harrowfielddentistry.com</div><div><b>Location</b>418 Larkmoor Ave. Fenwick,<br>Illinois 60412</div><div><b>Opening Hours</b>Mon to Sat 9:00 am to 12:30 pm<br>Mon to Sat 5:00 pm to 8:30 pm</div></div>
</section>

<section class="hero mid" style="left:1096px;top:341px;height:260px">
 <div class="ph" style="left:0;top:18px;width:462px;height:242px;background:linear-gradient(100deg,#2d8689 30%,#6fb3b4)" role="img" aria-label="Dentist in mask treating a patient"></div>
 <div class="topbar">Mon - Sat : 09:00 AM - 06:00 PM <span>+1 212 555 0192</span></div>
 <div class="nav" style="left:18px;top:25px;width:426px"><span class="logo">Harrowfield Dentistry</span><ul><li>Home</li><li>About us</li><li>Services</li><li>Testimonials</li><li>Case studies</li><li>Gallery</li><li>Blogs</li></ul><span class="btn">Book an appointment</span></div>
 <div class="hero-copy" style="left:57px;top:82px"><h2>Get your confident<br>smile now!</h2><p>Welcome to a place where excellence meets dentistry and patients of all ages experience wide range of personalised dental solutions.</p><span class="btn white">Start using Brightline</span></div>
</section>

<section class="hero mid" style="left:1597px;top:341px;height:270px">
 <div class="ph" style="left:0;top:18px;width:462px;height:252px;background:linear-gradient(100deg,#2d8689 30%,#6fb3b4)" role="img" aria-label="Dentist in mask treating a patient"></div>
 <div class="topbar" style="justify-content:space-between">Mon - Sat : 09:00 AM - 06:00 PM <span>☏ +1 212 555 0192 &nbsp; ⌖ 418 Larkmoor Ave. Fenwick, Illinois 60412</span></div>
 <div class="nav" style="left:18px;top:26px;width:426px"><span class="logo">Harrowfield Dentistry</span><ul><li>Home</li><li>About us</li><li>Services</li><li>Testimonials</li><li>Case studies</li><li>Gallery</li><li>Blogs</li></ul><span class="btn">Book an appointment</span></div>
 <div class="hero-copy" style="left:43px;top:73px"><div class="kick">Welcome to the Harrowfield</div><h2>Get your confident<br>smile now!</h2><p style="width:190px">At our practice, excellence in dentistry goes hand-in-hand with personalized care, offering patients of all ages a wide range of tailored dental solutions.</p><span class="btn white">Book an appointment</span><div class="rating">Patient Rating <b>5.0 ★★★★★</b> based on 492 reviews</div></div>
</section>

<section class="hero" style="left:1096px;top:633px;height:271px;background:var(--white)">
 <div class="a" style="left:0;top:31px;width:462px;height:193px;background:var(--teal)"></div>
 <div class="ph" style="left:285px;top:45px;width:115px;height:179px;background:linear-gradient(180deg,#3d8a8c,#e8eef0)" role="img" aria-label="Female dentist with arms crossed"></div>
 <div class="a" style="left:400px;top:78px;width:22px;height:22px;border-radius:50%;border:1px solid #5fa9ab"></div>
 <div class="a" style="left:278px;top:152px;width:22px;height:22px;border-radius:50%;border:1px solid #5fa9ab"></div>
 <div class="a" style="left:410px;top:192px;width:22px;height:22px;border-radius:50%;border:1px solid #5fa9ab"></div>
 <div class="nav" style="left:0;top:0;width:462px;height:31px;border-radius:0;padding:0 42px"><span class="logo">Harrowfield Dentistry</span><ul><li>Home</li><li>About us</li><li>Services</li><li>Testimonials</li><li>Case studies</li><li>Gallery</li><li>Blogs</li></ul><span class="btn">Contact Us</span></div>
 <div class="hero-copy" style="left:43px;top:69px"><div class="kick">Welcome to the Harrowfield</div><h2>Get your confident<br>smile now!</h2><p style="width:180px">At our practice, excellence in dentistry goes hand-in-hand with personalized care, offering patients of all ages a wide range of tailored dental solutions.</p><span class="btn">Book an appointment</span></div>
 <div class="info-strip" style="left:43px;top:233px;width:390px">
  <div><b>Contact Us</b>+1 212 555 0192<br>info@harrowfielddentistry.com</div><div><b>Location</b>418 Larkmoor Ave. Fenwick,<br>Illinois 60412</div><div><b>Opening Hours</b>Mon to Sat 9:00 am to 12:30 pm<br>Mon to Sat 5:00 pm to 8:30 pm</div></div>
</section>

<section class="hero" style="left:1597px;top:645px;height:259px">
 <div class="ph" style="left:300px;top:26px;width:162px;height:233px;background:linear-gradient(135deg,#4b8c8b,#b07a5e)" role="img" aria-label="Dentist examining a smiling patient"></div>
 <div class="nav" style="left:0;top:0;width:462px;height:26px;border-radius:0;padding:0 34px"><span class="logo">Harrowfield Dentistry</span><ul><li>Home</li><li>About us</li><li>Services</li><li>Testimonials</li><li>Case studies</li><li>Gallery</li><li>Blogs</li></ul><span class="btn">Contact Us</span></div>
 <div class="hero-copy" style="left:30px;top:66px"><div class="kick">Welcome to the Harrowfield</div><h2>Get your confident<br>smile now!</h2><p style="width:185px">At our practice, excellence in dentistry goes hand-in-hand with personalized care, offering patients of all ages a wide range of tailored dental solutions.</p><span class="btn white">Book an appointment</span><div class="rating">Patient Rating <b>5.0 ★★★★★</b> based on 492 reviews</div></div>
</section>

<section class="hero" style="left:1096px;top:937px;height:259px;background:var(--white)">
 <div class="a" style="left:0;top:0;width:462px;height:226px;background:var(--teal)"></div>
 <div class="topbar" style="justify-content:space-between">Mon - Sat : 09:00 AM - 06:00 PM <span>☏ +1 212 555 0192 &nbsp; ⌖ 418 Larkmoor Ave. Fenwick, Illinois 60412</span></div>
 <div class="nav" style="left:18px;top:19px;width:420px"><span class="logo">Harrowfield Dentistry</span><ul><li>Home</li><li>About us</li><li>Services</li><li>Testimonials</li><li>Case studies</li><li>Gallery</li><li>Blogs</li></ul><span class="btn">Contact Us</span></div>
 <div class="ph" style="left:262px;top:61px;width:172px;height:185px;border-radius:4px;background:linear-gradient(135deg,#cfd9d8,#4f8a78)" role="img" aria-label="Smiling man with shade guide"></div>
 <div class="a" style="left:351px;top:161px;width:98px;height:32px;background:var(--white);border-radius:3px;padding:4px 6px;font-size:4.5px;line-height:1.5"><span style="color:var(--accent);font-size:8px">“</span><br>Great care from friendly, skilled, and super gentle staff</div>
 <div class="hero-copy" style="left:51px;top:68px"><div class="kick">Welcome to the Harrowfield</div><h2>Get your confident<br>smile now!</h2><p style="width:185px">At our practice, excellence in dentistry goes hand-in-hand with personalized care, offering patients of all ages a wide range of tailored dental solutions.</p><span class="btn">Book an appointment</span></div>
 <div class="a" style="left:43px;top:233px;font-size:8px;font-weight:500">3.6k+<div style="font-size:4.5px;font-weight:400">Happy Clients</div></div>
 <p class="a small" style="left:96px;top:235px;width:130px">Lorem ipsum dolor sit amet consectetur adipiscing elit, sed do eiusmod tempor Lorem ipsum dolor text.</p>
</section>

<section class="hero" style="left:1597px;top:953px;height:207px">
 <div class="ph" style="left:260px;top:31px;width:202px;height:176px;background:linear-gradient(135deg,#2c7c7e,#b8434a)" role="img" aria-label="Smiling young woman"></div>
 <div class="nav" style="left:0;top:0;width:462px;height:31px;border-radius:0;padding:0 34px"><span class="logo">Harrowfield Dentistry</span><ul><li>Home</li><li>About us</li><li>Services</li><li>Testimonials</li><li>Case studies</li><li>Gallery</li><li>Blogs</li></ul><span class="btn">Book an appointment</span></div>
 <div class="hero-copy" style="left:57px;top:64px"><h2 style="font-size:17px">Get your confident<br>smile now!</h2><p>Welcome to a place where excellence meets dentistry and patients of all ages experience wide range of personalised dental solutions.</p><span class="btn">Start using Brightline</span></div>
</section>

</div>
</body></html>
```